Business Card: RW Office Partners - Your organised problem solver

Business Name: RW Office Partners
Website: www.rwofficepartners.com.au
Email: marisol@rwofficepartners.com.au
Mobile: 61 482 907 236
Facebook: @rwofficepartners
Instrgram: @rwofficepartners

Brading Colours:
HEX
#986474
#ddccd3
#7a8498
#c9d8e4
#000000
#ffffff

Tag Line: Your organised problem solver

Link to DRAFT website:
https://deskhelpcollective.wixsite.com/rw-office-partners

About Page from the website:
My name is Marisol Wrenfield, and I would love to assist you to become more productive in your day to day and achieve your business and personal goals.
My mission is to give you time, time to work on the important tasks of your business or to be able to spend more time with your family. I will take on the tasks you don’t have time for, don’t know well or simply don’t like to do.
I have an extensive background in Administration, Tender Coordination, Document Control, WHS and Quality Management working primarily in the Construction, Mining and Corporate World.
I am passionate about being organised, having order and making things in your life (and mine) easier! I love to watch something unfold and grow into something amazing! I am known for being the go-to problem solver, the organiser of all things, producing high standards of work even under pressure. I’m also a confident communicator, and I understand that you’re busy running your business.

Target Market(s)

Small to Medium Business who require assistance in their business by a virtual assistant.

Industry/Entity Type

Virtual Assistant

Contact Information for Business Card

Mobile: 61 482 907 236

Font styles to use
Sans Serif

Colors
ffffff

Requirements
Must have
• Branding Colours as outlined.
Contact Details as outlined.
Logo as provided.
Proper contact details - mobile, facebook, instragm, website.
Simple, Elegant, very clean looking.
Should not have
• Note cute with pictures.
Not too girly as still want to market to construction companies.

```html
<!DOCTYPE html>
<html lang="en">
<head>
<meta charset="utf-8">
<title>RW Office Partners – Business Card</title>
<link rel="stylesheet" href="https://fonts.googleapis.com/css2?family=Lato:wght@400;700&display=swap">
<style>
  :root {
    --mauve: #986474;
    --slate: #7a8498;
    --ink: #2b2b2b;
    --white: #ffffff;
    --backdrop: #e9e6e8;
  }
  * { box-sizing: border-box; margin: 0; padding: 0; }
  html, body { width: 1200px; height: 900px; overflow: hidden; }
  body {
    background: var(--backdrop);
    font-family: "Lato", Arial, sans-serif;
    position: relative;
  }
  .card {
    position: absolute;
    left: 320px;
    width: 560px;
    height: 342px;
    overflow: hidden;
    box-shadow: 0 6px 18px rgba(0,0,0,0.18);
  }
  /* Front */
  .card--front { top: 88px; background: var(--mauve); color: var(--white); }
  .front__brand {
    position: absolute;
    left: 96px; top: 104px;
    font-size: 44px;
    font-weight: 700;
    line-height: 1.08;
    letter-spacing: 0.5px;
    color: var(--white);
  }
  .front__social {
    position: absolute;
    right: 44px; bottom: 40px;
    display: flex; align-items: center; gap: 10px;
    font-size: 15px; font-weight: 700;
  }
  .front__social-label { margin-right: 14px; }
  .social-square {
    width: 20px; height: 20px;
    border: 2px solid var(--white);
    border-radius: 4px;
  }
  .social-square--filled { background: var(--white); }
  .front__handle { font-weight: 400; }

  /* Back */
  .card--back { top: 470px; background: var(--white); }
  .back__bands { position: absolute; inset: 0; }
  .back__brand {
    position: absolute;
    left: 52px; top: 52px;
    font-size: 32px;
    font-weight: 700;
    line-height: 1.1;
    color: var(--mauve);
    letter-spacing: 0.4px;
  }
  .contact-list {
    position: absolute;
    left: 60px; top: 160px;
    list-style: none;
  }
  .contact-item {
    display: flex; align-items: center; gap: 12px;
    height: 27px;
    font-size: 16px;
    font-weight: 700;
    color: var(--ink);
  }
  .contact-icon { width: 20px; height: 20px; flex: none; }
</style>
</head>
<body>

<section class="card card--front" aria-label="Card front">
  <h1 class="front__brand">RW Office<br>Partners</h1>
  <div class="front__social">
    <span class="front__social-label">Follow Us</span>
    <span class="social-square social-square--filled" aria-hidden="true"></span>
    <span class="social-square" aria-hidden="true"></span>
    <span class="front__handle">/ @rwofficepartners</span>
  </div>
</section>

<section class="card card--back" aria-label="Card back">
  <svg class="back__bands" viewBox="0 0 560 342" aria-hidden="true">
    <polygon points="0,318 364,318 384,270 388,270 358,342 0,342" fill="var(--mauve)"/>
    <polygon points="394,270 560,270 560,342 364,342" fill="var(--slate)"/>
  </svg>

  <div class="back__brand">RW Office<br>Partners</div>

  <ul class="contact-list">
    <li class="contact-item">
      <svg class="contact-icon" viewBox="0 0 20 20" aria-hidden="true">
        <path d="M5 2 L8 6 L6.5 8 C7.5 10.5 9.5 12.5 12 13.5 L14 12 L18 15 L16 18 C9 18 2 11 2 4 Z" fill="var(--mauve)"/>
      </svg>
      <span>61 482 907 236</span>
    </li>
    <li class="contact-item">
      <svg class="contact-icon" viewBox="0 0 20 20" aria-hidden="true">
        <rect x="1.5" y="4" width="17" height="12" fill="var(--mauve)"/>
        <polyline points="1.5,4 10,11 18.5,4" fill="none" stroke="var(--white)" stroke-width="1.4"/>
      </svg>
      <span>marisol@rwofficepartners.com.au</span>
    </li>
    <li class="contact-item">
      <svg class="contact-icon" viewBox="0 0 20 20" aria-hidden="true">
        <circle cx="10" cy="10" r="8.5" fill="var(--mauve)"/>
        <g fill="none" stroke="var(--white)" stroke-width="1">
          <ellipse cx="10" cy="10" rx="3.6" ry="8.5"/>
          <line x1="1.5" y1="10" x2="18.5" y2="10"/>
          <line x1="3" y1="6" x2="17" y2="6"/>
          <line x1="3" y1="14" x2="17" y2="14"/>
        </g>
      </svg>
      <span>www.rwofficepartners.com.au</span>
    </li>
    <li class="contact-item">
      <svg class="contact-icon" viewBox="0 0 20 20" aria-hidden="true">
        <rect x="2" y="2" width="16" height="16" rx="3" fill="none" stroke="var(--mauve)" stroke-width="2"/>
      </svg>
      <span>@rwofficepartners</span>
    </li>
    <li class="contact-item">
      <svg class="contact-icon" viewBox="0 0 20 20" aria-hidden="true">
        <rect x="1" y="1" width="18" height="18" rx="2" fill="var(--mauve)"/>
      </svg>
      <span>@rwofficepartners</span>
    </li>
  </ul>
</section>

</body>
</html>
```